Satchel & Sundial needs new business card design

I need a new business card design. I'm looking for out-of-the-box design which represents the freedom of being a location independent entrepreneur.
I offer coaching, retreats and trips.
I would like to see designs with and without the photo.
Colors I use are black (#000000), green (#25A796) and brown (#D7C38C)
Website satchelandsundial.example

Target Market(s)

location independent entrepreneurs, digital nomads, people looking to swap the 9 to 5 for a lifestyle business

Industry/Entity Type

Business

Contact Information for Business Card

Dorota Falkner
Your Lifestyle Business Coach, Retreat & Trip Leader
http://satchelandsundial.example
hello@satchelandsundial.example
Live a life you don't need a holiday from

Font styles to use
Serif
Sans Serif

Requirements
Must have
• One side should contain only the logo. I would also consider having the "Live a life you don't need a holiday from" on that side too (depending on how it looks)
• Please show both sides on the designs.

```html
<!DOCTYPE html>
<html lang="en">
<head>
<meta charset="utf-8">
<title>Satchel &amp; Sundial — Business Card</title>
<link href="https://fonts.googleapis.com/css2?family=Roboto+Condensed:wght@400;700&display=swap" rel="stylesheet">
<style>
  :root {
    --backdrop: #e4e4e4;
    --card: #f7f7f6;
    --card-edge: #ececea;
    --ink: #1c1c1c;
    --teal: #25a796;
    --teal-deep: #14897a;
    --sand: #d7c38c;
    --photo-leaf: #7d9a6a;
    --photo-shade: #5f6f55;
  }
  * { margin: 0; padding: 0; box-sizing: border-box; }
  html, body {
    width: 1200px; height: 576px; overflow: hidden;
    background: var(--backdrop);
    font-family: "Roboto Condensed", "Arial Narrow", sans-serif;
  }
  .stage { position: relative; width: 1200px; height: 576px; }
  .card {
    position: absolute; top: 138px;
    width: 484px; height: 294px;
    background: linear-gradient(180deg, #fbfbfa 0%, var(--card) 60%, var(--card-edge) 100%);
    border-radius: 8px;
    box-shadow: 0 2px 4px rgba(0,0,0,.25);
    overflow: hidden;
  }
  .card--front { left: 82px; }
  .card--back { left: 602px; width: 481px; }

  /* front */
  .brand-name {
    position: absolute; left: 0; right: 0; top: 108px;
    text-align: center;
    font-weight: 700; font-size: 42px; letter-spacing: 1px;
    text-transform: uppercase; color: var(--ink);
  }
  .front-web {
    position: absolute; left: 0; right: 0; top: 253px;
    display: flex; justify-content: center; align-items: center; gap: 12px;
    font-size: 12px; color: var(--ink);
  }
  .front-web .rule { width: 46px; height: 2px; background: var(--sand); border-radius: 2px; }
  .front-web .domain { color: var(--teal); }

  /* back */
  .photo-art { position: absolute; inset: 0; }
  .person-name {
    position: absolute; left: 28px; top: 34px;
    font-weight: 700; font-size: 22px; color: var(--teal);
    text-transform: uppercase; letter-spacing: .3px;
  }
  .role { position: absolute; left: 28px; top: 60px; font-size: 12px; line-height: 15px; color: var(--ink); }
  .contacts { position: absolute; left: 28px; top: 154px; list-style: none; }
  .contacts li { display: flex; align-items: center; gap: 7px; height: 20.5px; font-size: 13px; color: var(--ink); }
  .contacts svg { width: 11px; height: 11px; flex: none; }
  .tagline { position: absolute; left: 28px; top: 236px; font-size: 14px; color: var(--teal); }
</style>
</head>
<body>
<main class="stage">

  <section class="card card--front" aria-label="Card front">
    <h1 class="brand-name">Satchel &amp; Sundial</h1>
    <p class="front-web">
      <span class="rule"></span>
      <span>www.<span class="domain">satchelandsundial</span>.example</span>
      <span class="rule"></span>
    </p>
  </section>

  <section class="card card--back" aria-label="Card back">
    <svg class="photo-art" viewBox="0 0 481 294" width="481" height="294">
      <defs>
        <linearGradient id="photoTone" x1="0" y1="0" x2="0.3" y2="1">
          <stop offset="0" stop-color="#8ea97c"/>
          <stop offset=".5" stop-color="#6d8460"/>
          <stop offset="1" stop-color="#5a6a52"/>
        </linearGradient>
      </defs>
      <path d="M296 0 Q204 130 258 215 Q222 120 308 0 Z" fill="var(--teal)"/>
      <path role="img" aria-label="Photo of the coach sitting on a wooden rail among trees, holding a small sign"
            d="M302 0 Q210 150 286 294 L481 294 L481 0 Z" fill="url(#photoTone)"/>
    </svg>

    <h2 class="person-name">Dorota Falkner</h2>
    <p class="role">Your Lifestyle Business Coach<br>Retreat &amp; Trip Leader</p>

    <ul class="contacts">
      <li>
        <svg viewBox="0 0 12 12"><rect x="0.5" y="2" width="11" height="8" fill="var(--teal)"/><path d="M0.5 2 L6 6.5 L11.5 2" stroke="#fff" stroke-width="1" fill="none"/></svg>
        hello@satchelandsundial.example
      </li>
      <li>
        <svg viewBox="0 0 12 12"><circle cx="6" cy="6" r="5" fill="none" stroke="var(--teal)" stroke-width="1.3"/><ellipse cx="6" cy="6" rx="2.2" ry="5" fill="none" stroke="var(--teal)" stroke-width="1"/><line x1="1" y1="6" x2="11" y2="6" stroke="var(--teal)" stroke-width="1"/></svg>
        www.satchelandsundial.example
      </li>
      <li>
        <svg viewBox="0 0 12 12"><rect x="1" y="1" width="10" height="10" rx="2" fill="var(--teal)"/></svg>
        /satchelandsundial
      </li>
    </ul>

    <p class="tagline">Live a life you don't need a holiday from</p>
  </section>

</main>
</body>
</html>
```